Bright Harbor Design

We need a web design for our startup company based in Zurich, Switzerland called Bright Harbor. We offer professional flirt and dating advice, self development with seminars and practical coachings.

The final website aims for two capital goals. First, it will contain text, pictures and video based content presenting and advertising our services. Furthermore, we want to bind our costumers with a plattform offering them to share their expiriences related with our services.

The targeted group will be men from 25 to 40 years.
Updates

The design requires also a register-box to put in the clients Name and Email

I need (besides of the "email registration box") a "Video Gallery", "Blog" and "Agenda (with the next events to come)"

Reason: I want to make a poll now

Target Market(s)

Guys around 25 to 40 years who want to improve their social lifestyle

Industry/Entity Type

Advertising

Requirements
Must have
• First and foremost, the design must transfer strong emotions and suggest an attractive social lifestyle.

The design should not be overloaded with content but should include pictures, videos and text.

The design should present a modern, urban lifestyle.
Nice to have
• There is a logo attached to the assignement. However, if you have a good idea for an improved or different logo, please do not hesitate to design your ideas.

```html
<!DOCTYPE html>
<html lang="en">
<head>
<meta charset="utf-8">
<title>Bright Harbor</title>
<link href="https://fonts.googleapis.com/css2?family=Arimo:wght@400;700&display=swap" rel="stylesheet">
<style>
:root{
  --navy:#17365d;
  --navy-dark:#0f2747;
  --title:#2f5d8c;
  --link:#3a6ea5;
  --text:#6a6a6a;
  --dark:#333;
  --line:#e4e4e4;
  --band:#ececec;
  --footer:#303030;
  --footer-base:#262626;
  --footer-text:#d8d8d8;
  --footer-title:#7fb0e0;
  --cyan:#36b4dc;
  --ad:#1f7cc4;
  --ad-lime:#e9f7a8;
}
*{margin:0;padding:0;box-sizing:border-box}
html,body{width:862px;height:1200px;overflow:hidden}
body{position:relative;background:#fff;font-family:"Arimo",Arial,sans-serif;color:var(--text)}
.abs{position:absolute}
.topbar{left:0;top:0;width:862px;height:8px;background:var(--navy)}
.header{left:0;top:8px;width:862px;height:132px;background:linear-gradient(#f2f2f2,#e6e6e6)}
.account{left:660px;top:8px;width:138px;height:23px;background:var(--navy);clip-path:polygon(0 0,100% 0,92% 100%,8% 100%);color:#fff;font-size:9px;font-weight:700;display:flex;justify-content:center;gap:18px;align-items:center}
.logo{left:64px;top:22px;display:flex;align-items:center;gap:8px;color:var(--navy);font-size:22px;font-weight:700}
.logo .mark{width:26px;height:26px;background:var(--navy);border-radius:50%}
.ad{left:447px;top:37px;width:351px;height:44px;background:var(--ad);color:#fff}
.ad .name{position:absolute;left:9px;top:2px;font-size:26px;font-weight:700}
.ad .tag{position:absolute;left:14px;top:32px;font-size:8px}
.ad .box{position:absolute;left:248px;top:7px;width:95px;height:29px;background:var(--ad-lime);font-size:6.5px;color:#6a7a20;padding:2px 5px}
.ad .box .in{position:absolute;left:4px;top:15px;width:58px;height:10px;background:#fff}
.ad .box .btn{position:absolute;left:66px;top:15px;width:24px;height:10px;background:#8cc63f;color:#fff;text-align:center;font-size:6px;line-height:10px}
.nav{left:63px;top:97px;width:735px;height:41px;background:var(--navy);border-radius:6px 6px 0 0;display:flex;align-items:center;color:#fff;font-size:10.5px}
.nav span{padding:0 19px;height:41px;line-height:41px;border-right:1px solid #2a4a74}
.nav .home{background:#fff;color:var(--navy);border-radius:6px 0 0 0;width:68px;padding:0;text-align:center}
.search{left:642px;top:105px;width:148px;height:24px;background:#fff;border-radius:12px;font-size:9px;color:#aaa;padding:8px 12px}
.search .go{position:absolute;right:3px;top:3px;width:18px;height:18px;border-radius:50%;background:var(--navy)}
.hero{left:63px;top:150px;width:735px;height:260px;background:#f4f4f4;box-shadow:0 6px 8px rgba(0,0,0,.25)}
.hero-photo{left:70px;top:155px;width:722px;height:250px;background:linear-gradient(100deg,#6b6660 0%,#8a8780 35%,#b4b0a8 60%,#7d8a88 85%,#5a6c68 100%)}
.caption{left:81px;top:352px;width:356px;height:41px;background:rgba(20,20,20,.85);color:#fff;font-size:15.5px;font-weight:700;line-height:41px;padding-left:21px}
.caption .arrow{position:absolute;right:0;top:0;width:28px;height:41px;border-left:1px solid #777}
h2{position:absolute;font-weight:400;color:var(--title);font-size:15px}
.welcome-text{left:64px;top:467px;width:500px;font-size:9.2px;line-height:16.5px;text-align:justify}
.tips{left:573px;top:443px;width:225px;height:86px;background:#f2f2f2}
.tips .photo{position:absolute;left:0;top:0;width:62px;height:86px;background:linear-gradient(#a07a60,#e9d9cc)}
.tips h3{position:absolute;left:77px;top:8px;font-weight:400;color:var(--title);font-size:14.5px;width:135px;border-bottom:1px solid #ccc;padding-bottom:5px}
.tips p{position:absolute;left:78px;top:38px;width:140px;font-size:9px;line-height:13.5px}
.tips a{color:var(--link)}
.divider{left:64px;top:544px;width:734px;height:1px;background:var(--line)}
.circle{width:13px;height:13px;border-radius:50%;background:#9a9a9a}
.band{height:7px;background:var(--band)}
.card{left:64px;width:498px;height:113px;border:1px solid var(--line);background:#fff}
.card .photo{position:absolute;left:6px;top:6px;width:101px;height:100px;border:2px solid #eee}
.card h4{position:absolute;left:119px;top:8px;font-weight:400;color:var(--link);font-size:11px}
.card p{position:absolute;left:119px;top:29px;width:370px;font-size:9.2px;line-height:15px;text-align:justify}
.card .meta{position:absolute;left:119px;top:94px;font-size:9.3px;color:#333}
.card .meta a{color:var(--link)}
.video{left:575px;top:608px;width:223px;height:113px;border:1px solid var(--line)}
.video .thumb{position:absolute;left:8px;top:8px;width:97px;height:97px;background:linear-gradient(135deg,#2a2a2a,#8a8a8a)}
.video .play{position:absolute;left:32px;top:32px;width:32px;height:32px;border-radius:50%;background:rgba(255,255,255,.55)}
.video h4{position:absolute;left:116px;top:18px;width:100px;font-weight:400;color:var(--link);font-size:11px;line-height:17px}
.video p{position:absolute;left:116px;top:55px;font-size:9.3px}
.video .share{position:absolute;left:116px;top:84px;display:flex;gap:4px;font-size:5.5px;color:#3b5a8a}
.video .share span{border:1px solid #ccc;padding:1px 3px;background:#f5f5f5}
.members{left:575px;top:794px;display:grid;grid-template-columns:repeat(5,40px);grid-auto-rows:40px;gap:2px 5px}
.members span{border:2px solid #ddd;border-radius:2px}
.footer{left:0;top:978px;width:862px;height:174px;background:var(--footer);border-top:2px solid #111}
.footer-base{left:0;top:1152px;width:862px;height:48px;background:var(--footer-base);color:#aaa;font-size:8.8px;text-align:center;line-height:56px}
.ftitle{position:absolute;color:var(--footer-title);font-size:12px}
.links{position:absolute;top:1022px;list-style:none;color:var(--footer-text);font-size:9.2px;line-height:21px}
.links li::before{content:"•";margin-right:5px;color:#aaa}
.vline{top:993px;width:1px;height:148px;background:#4a4a4a}
.field{left:455px;width:163px;height:20px;background:#fff;font-size:8px;color:#333;padding:6px 12px}
.submit{left:568px;top:1086px;width:50px;height:21px;background:var(--cyan);color:#fff;font-size:10.5px;font-weight:700;text-align:center;line-height:21px}
.social{position:absolute;left:650px;display:flex;align-items:center;gap:18px;font-size:9px;color:var(--footer-text)}
.social i{width:18px;height:18px;background:#4a78b8;display:block}
.social b{font-weight:400;color:var(--footer-title);font-size:11px;margin-left:4px}
</style>
</head>
<body>
<div class="abs topbar"></div>
<div class="abs header"></div>
<div class="abs account"><span>REGISTER</span><span>LOGIN</span></div>
<div class="abs logo"><span class="mark"></span>Bright Harbor</div>
<div class="abs ad"><span class="name">SoundCrate.net</span><span class="tag">100% Free Loop &amp; Sample Directory</span>
<div class="box">Search Loops<span class="in"></span><span class="btn">Search</span></div></div>
<nav class="abs nav"><span class="home">HOME</span><span>ABOUT US</span><span>TIPS</span><span>PROFILE</span><span>COMMUNITY</span><span>BLOG</span><span>CONTACT US</span></nav>
<div class="abs search">Search<span class="go"></span></div>

<div class="abs hero"></div>
<div class="abs hero-photo" role="img" aria-label="Photo of a man and a woman talking on a busy city street"></div>
<div class="abs caption">DON’T STAY ALONE....&nbsp;&nbsp; JUST TALK
<svg class="arrow" viewBox="0 0 28 41"><path d="M10 13l8 7.5-8 7.5" fill="none" stroke="#fff" stroke-width="3.5"/></svg></div>

<h2 style="left:65px;top:442px">Welcome to Bright Harbor</h2>
<p class="abs welcome-text">Phasellus erat felis, ultricies nec eleifend viverra, tempus nec nibh. Phasellus at risus a est varius dictum sed convallis arcu. Aliquam rhoncus, purus in commodo aliquet, elit lectus laoreet enim, sit amet facilisis est nisi in orci. Pellen tesque malesuada imperdiet enim quis elementum. Cras sapien eros, egestas et ultricies tempus, vehicula ut neque. Nunc elit orci, convallis at interdum in, lobortis non sapien.</p>
<div class="abs tips"><div class="photo" role="img" aria-label="Portrait photo of a woman with short hair"></div>
<h3>Latest Tips</h3><p>Curabitur lectus erat, commodo eu sodales eu, dapibus quis dui. <a>more...</a></p></div>
<div class="abs divider"></div>

<h2 style="left:65px;top:562px">Latest Topics</h2>
<div class="abs circle" style="left:549px;top:563px"></div>
<div class="abs band" style="left:64px;top:590px;width:498px"></div>

<div class="abs card" style="top:608px"><div class="photo" role="img" aria-label="Photo of a smiling couple facing each other"></div>
<h4>Curabitur ultrices lobortis arcu eu sagittis.</h4>
<p>Curabitur lectus erat, commodo eu sodales eu, dapibus quis dui. Mauris blandit orci commodo felis pellentesque sit amet pretium tellus varius. Quisque justo neque, facili sis a scelerisque at, pulvinar eu mauris. Phasellus ac augue et nibh sodales tempus. Aliquam rhoncus, purus in commodo aliquet.</p>
<div class="meta">Mar-8-13 &nbsp;&nbsp; | &nbsp;&nbsp; 40 LIkes &nbsp;&nbsp; | &nbsp;&nbsp; 12 Comments &nbsp;&nbsp; | &nbsp;&nbsp; <a>View more</a></div></div>
<div class="abs card" style="top:729px"><div class="photo" role="img" aria-label="Photo of a man offering a red rose to a woman"></div>
<h4>Curabitur ultrices lobortis arcu eu sagittis.</h4>
<p>Curabitur lectus erat, commodo eu sodales eu, dapibus quis dui. Mauris blandit orci commodo felis pellentesque sit amet pretium tellus varius. Quisque justo neque, facili sis a scelerisque at, pulvinar eu mauris. Phasellus ac augue et nibh sodales tempus. Aliquam rhoncus, purus in commodo aliquet.</p>
<div class="meta">Mar-8-13 &nbsp;&nbsp; | &nbsp;&nbsp; 40 LIkes &nbsp;&nbsp; | &nbsp;&nbsp; 12 Comments &nbsp;&nbsp; | &nbsp;&nbsp; <a>View more</a></div></div>
<div class="abs card" style="top:850px"><div class="photo" role="img" aria-label="Photo of a woman using a laptop"></div>
<h4>Curabitur ultrices lobortis arcu eu sagittis.</h4>
<p>Curabitur lectus erat, commodo eu sodales eu, dapibus quis dui. Mauris blandit orci commodo felis pellentesque sit amet pretium tellus varius. Quisque justo neque, facili sis a scelerisque at, pulvinar eu mauris. Phasellus ac augue et nibh sodales tempus. Aliquam rhoncus, purus in commodo aliquet.</p>
<div class="meta">Mar-8-13 &nbsp;&nbsp; | &nbsp;&nbsp; 40 LIkes &nbsp;&nbsp; | &nbsp;&nbsp; 12 Comments &nbsp;&nbsp; | &nbsp;&nbsp; <a>View more</a></div></div>

<h2 style="left:576px;top:562px">Latest Videos</h2>
<div class="abs circle" style="left:784px;top:563px"></div>
<div class="abs band" style="left:575px;top:590px;width:224px"></div>
<div class="abs video"><div class="thumb" role="img" aria-label="Black and white video still of a thoughtful woman"></div>
<svg class="play" viewBox="0 0 32 32"><path d="M12 9l11 7-11 7z" fill="#333"/></svg>
<h4>Pellentesque male suada.</h4><p>Quisque justo neque.</p>
<div class="share"><span>Like</span><span>3k</span><span>Post</span><span>316</span></div></div>

<h2 style="left:576px;top:746px">Members of Bright Harbor</h2>
<div class="abs band" style="left:575px;top:774px;width:224px"></div>
<div class="abs members" role="img" aria-label="Grid of member profile photos">
<span style="background:#b89a6a"></span><span style="background:#8a8a8e"></span><span style="background:#6b5040"></span><span style="background:#2a3550"></span><span style="background:#4a3a2a"></span>
<span style="background:#5a6fa0"></span><span style="background:#9a8e88"></span><span style="background:#c06a2a"></span><span style="background:#7a80a8"></span><span style="background:#8a4a20"></span>
<span style="background:#a03a5a"></span><span style="background:#c07060"></span><span style="background:#d8c8b0"></span><span style="background:#b09098"></span><span style="background:#9a4050"></span>
<span style="background:#b82a2a"></span><span style="background:#d8c8c0"></span><span style="background:#c09060"></span><span style="background:#3a5a5a"></span><span style="background:#5a7aa0"></span>
</div>

<footer class="abs footer"></footer>
<div class="ftitle" style="left:66px;top:995px">Quick Links</div>
<ul class="links" style="left:66px"><li>Integer lobortis</li><li>Curabitur ac</li><li>Phasellus tellus nisl</li><li>Aenean fringilla</li><li>Vestibulum</li><li>Aliquam commodo</li></ul>
<ul class="links" style="left:195px"><li>Integer lobortis</li><li>Curabitur ac</li><li>Phasellus tellus nisl</li><li>Aenean fringilla</li><li>Vestibulum</li><li>Aliquam commodo</li></ul>
<ul class="links" style="left:323px"><li>Integer lobortis</li><li>Curabitur ac</li><li>Phasellus tellus nisl</li><li>Aenean fringilla</li><li>Vestibulum</li><li>Aliquam commodo</li></ul>
<div class="abs vline" style="left:432px"></div>
<div class="ftitle" style="left:455px;top:995px">Email Signup</div>
<div class="abs field" style="top:1025px">Name</div>
<div class="abs field" style="top:1056px">Email ID</div>
<div class="abs submit">SUBMIT</div>
<div class="abs vline" style="left:632px"></div>
<div class="ftitle" style="left:650px;top:995px">Connect with us</div>
<div class="social" style="top:1025px"><i></i><span>Join with us on<b>Gatherly</b></span></div>
<div class="social" style="top:1055px"><i style="background:#3aa8d8"></i><span>Follow us on<b>Chirpline</b></span></div>
<div class="social" style="top:1085px"><i style="background:#2a6a9a"></i><span>Share on<b>ProLink</b></span></div>
<div class="social" style="top:1115px"><i style="background:#c33"></i><span>Watch on<b>ViewStream</b></span></div>
<div class="abs footer-base">Copyright &nbsp;© &nbsp;2013 &nbsp;&nbsp; www.brightharbor.com &nbsp;&nbsp; All rights reserved.</div>
</body>
</html>
```